Ward Compass Business Card Design*

We need a business card design for our company Ward Compass. Our company is specialized in providing online consulting services regarding medical institutions, hospitals and doctors. We work with patients worldwide looking to choose between healthcare providers. We have a website you may use as a reference, where we list doctors and clinics worldwide. So we target Medical providers as well as patients worldwide.
Target Market(s)
Medical Providers and patients around the world
Industry/Entity Type
Medical
Contact Information for Business Card
Salwa Kettani
CEO
+90 612 348 2175
info@wardcompass.example
www.wardcompass.example
14 Annakhil 7 H.R.B. Rabat, Morocco
Requirements
Must have
- Company logo/name on one full side, personal info and smaller logo and company name on the other side.
Nice to have
- Smart and elegant design

```html
<!DOCTYPE html>
<html lang="en">
<head>
<meta charset="utf-8">
<title>Ward Compass — Business Card</title>
<link rel="stylesheet" href="https://fonts.googleapis.com/css2?family=Montserrat:wght@400;500;700&display=swap">
<style>
  :root {
    --navy: #10335f;
    --navy-deep: #0b2749;
    --grey-arc: #8c8c8c;
    --grey-text: #3a3a3a;
    --paper: #ffffff;
    --paper-shade: #ececec;
    --backdrop: #e4e5e8;
    --social: #c9d3e0;
  }
  html, body {
    margin: 0;
    width: 1200px;
    height: 997px;
    overflow: hidden;
    background: var(--backdrop);
    font-family: "Montserrat", Arial, sans-serif;
  }
  .sheet {
    position: relative;
    width: 1200px;
    height: 997px;
  }
  .card {
    position: absolute;
    left: 250px;
    width: 700px;
    height: 400px;
    background: linear-gradient(160deg, var(--paper) 40%, var(--paper-shade));
    box-shadow: 0 10px 30px rgba(0,0,0,0.18);
    overflow: hidden;
  }
  .card--front { top: 55px; }
  .card--back { top: 530px; }
  .card__waves {
    position: absolute;
    inset: 0;
    width: 700px;
    height: 400px;
  }
  .brand {
    position: absolute;
    display: flex;
    align-items: center;
    gap: 14px;
    color: var(--navy);
    font-weight: 700;
    letter-spacing: 1px;
    text-transform: uppercase;
  }
  .brand__dot {
    border-radius: 50%;
    border: 0;
    background: var(--navy);
  }
  .card--front .brand { left: 90px; top: 140px; font-size: 34px; }
  .card--front .brand__dot { width: 58px; height: 58px; }
  .card--back .brand { left: 40px; top: 48px; font-size: 26px; }
  .card--back .brand__dot { width: 46px; height: 46px; }
  .front__url {
    position: absolute;
    left: 36px;
    bottom: 30px;
    color: var(--paper);
    font-size: 17px;
    font-weight: 500;
    letter-spacing: 0.5px;
  }
  .person {
    position: absolute;
    left: 44px;
    top: 140px;
  }
  .person__name {
    margin: 0;
    color: var(--navy);
    font-size: 19px;
    font-weight: 700;
    letter-spacing: 0.5px;
    text-transform: uppercase;
  }
  .person__role {
    margin: 2px 0 0;
    color: var(--grey-text);
    font-size: 13px;
    font-weight: 700;
  }
  .contacts {
    position: absolute;
    left: 44px;
    top: 232px;
    margin: 0;
    padding: 0;
    list-style: none;
    color: var(--grey-text);
    font-size: 15px;
  }
  .contacts li {
    display: flex;
    align-items: center;
    gap: 12px;
    height: 26px;
  }
  .contacts svg { width: 15px; height: 15px; fill: var(--navy); }
  .social {
    position: absolute;
    right: 24px;
    top: 262px;
    display: flex;
    gap: 8px;
  }
  .social span {
    width: 24px;
    height: 24px;
    border-radius: 50%;
    background: var(--social);
  }
</style>
</head>
<body>
<main class="sheet">

  <section class="card card--front" aria-label="Card front">
    <svg class="card__waves" viewBox="0 0 700 400" aria-hidden="true">
      <path d="M0 300 C 250 300 500 240 700 130 L700 400 L0 400 Z" fill="var(--navy)"/>
      <path d="M0 270 C 260 272 500 215 700 105" fill="none" stroke="var(--grey-arc)" stroke-width="11"/>
    </svg>
    <div class="brand"><span class="brand__dot"></span>Ward Compass</div>
    <p class="front__url" style="margin:0">www.wardcompass.example</p>
  </section>

  <section class="card card--back" aria-label="Card back">
    <svg class="card__waves" viewBox="0 0 700 400" aria-hidden="true">
      <path d="M0 368 C 320 372 560 300 700 110 L700 400 L0 400 Z" fill="var(--navy)"/>
      <path d="M0 345 C 330 350 560 250 655 0" fill="none" stroke="var(--grey-arc)" stroke-width="10"/>
    </svg>
    <div class="brand"><span class="brand__dot"></span>Ward Compass</div>

    <div class="person">
      <p class="person__name">Salwa Kettani</p>
      <p class="person__role">CEO</p>
    </div>

    <ul class="contacts">
      <li>
        <svg viewBox="0 0 16 16" aria-hidden="true"><path d="M3 1h3l1.5 4-2 1.3a9 9 0 0 0 4.2 4.2L11 8.5l4 1.5v3a2 2 0 0 1-2 2A12 12 0 0 1 1 3a2 2 0 0 1 2-2z"/></svg>
        +90 612 348 2175
      </li>
      <li>
        <svg viewBox="0 0 16 16" aria-hidden="true"><path d="M1 3h14v10H1z M2 4l6 5 6-5" fill="none" stroke="var(--navy)" stroke-width="1.6"/></svg>
        info@wardcompass.example
      </li>
      <li>
        <svg viewBox="0 0 16 16" aria-hidden="true"><circle cx="8" cy="8" r="7"/><path d="M1 8h14M8 1c-3 3-3 11 0 14M8 1c3 3 3 11 0 14" fill="none" stroke="#fff" stroke-width="1"/></svg>
        www.wardcompass.example
      </li>
    </ul>

    <div class="social" aria-label="Social channels">
      <span></span><span></span><span></span><span></span><span></span><span></span>
    </div>
  </section>

</main>
</body>
</html>
```